Residential Mortgage Leader needs Wordpress Design

Looking for a home page website design for a client. We develop using the WordPress platform and would prefer the design be at least loosely based on an existing WordPress template. Attached files have many notes from our creative brief with client. The site must be responsive. Approved, basic wireframe attached. There is room for interpretation.

Existing web site: http://www.marisolkettering.example/

The Marisol Kettering Team relies on strong systems to deliver an on-time, done-right, friendly experience. Marisol offers mortgages and refinancing services throughout the United States. She is a successful Brookvale Funding agent who strives to be an active part of her community. She would like to focus the site on her team, rather than just her.

Difference makers...
When you work with the Marisol Kettering team you get a high level of expertise and a friendly experience.

She has amazing credentials. Marisol is widely recognized as a top producer for her company, and has earned a number of awards and honors for her customer service.

Marisol's team is very engaged and enjoys sharing social comments or photos from their community.

Imagery:
* Friendly, warm imagery, preferably of her team or an image to represent her team
* Clean and crisp
* Professional / Experts in mortgage and refinance
* Clean / Good use of white space
Updates

When possible, please use imagery from the DFW area. The client mentioned they would prefer not to see stock images. Thanks.

Amend that- creative use of stock images, however, is fine. A few designs have used stock imagery, but in a well-considered manner.

We added some photos and graphics that are local. We are Dallas / Ft. Worth, Plano, Frisco, Texas. We also added some examples of photos to use for the "In the Community" area. Stock photos of business folks just doesn't fit there. Thanks!

Target Market(s)

They service a lot of builders, but also work with homeowners. Their typical client is usually a woman searching for mortgage services online. She typically has a family and may refer her husband to Marisol's team. Keep in mind, however, they also see a number of other scenarios. Most of their clients are middle to high-end borrowers.

Industry/Entity Type

It Company

Requirements
Must have
• Design should be developed using program such as Photoshop or Fireworks or Illustrator as last preference. Ideally, the design would be based on an existing responsive WordPress theme, which we would customize. You must include the name of the target theme. The footer should include lots of space for disclaimers and legal language. Site navigation should include these choices: "Home, About, Builders, Mortgage Info, Approval, Blog, Contact"
Nice to have
• Blog, social media and photos area. Use of the already approved style prototype with colors and fonts (Lato- a Google font, Times New Roman and Cookie-a decorative Google font). However, we are open to interpretation.
Should not have
• Hard to read fonts or a lack of white space.

```html
<!DOCTYPE html>
<html lang="en">
<head>
<meta charset="utf-8">
<title>Marisol Kettering Team | Brookvale Funding</title>
<link rel="stylesheet" href="https://fonts.googleapis.com/css2?family=Open+Sans:wght@400;600;700&display=swap">
<style>
:root{
  --red:#c4321f;
  --slate:#4d5f7e;
  --grey-dark:#57585a;
  --grey-footer:#5c5d5f;
  --grey-bar:#4a4b4d;
  --text:#555;
  --link-blue:#8fa3d9;
}
*{box-sizing:border-box;margin:0;padding:0}
html,body{width:1108px;height:1200px;overflow:hidden;background:#fff}
body{font-family:"Open Sans",Arial,sans-serif;color:var(--text);position:relative}
.wrap{position:absolute;left:111px;width:886px}

/* header */
.brand{top:36px;display:flex;flex-direction:column}
.brand-name{font-size:29px;font-weight:700;color:var(--red);letter-spacing:-.5px;line-height:1}
.brand-tag{font-size:13px;color:var(--grey-dark);margin-top:4px}
.contact-top{top:38px;text-align:right;font-size:13px;font-weight:600;color:#555;line-height:29px}
.contact-top .hl{color:var(--red)}

.hero{position:absolute;top:119px;left:0;width:1108px;height:335px;background:var(--slate)}
.hero-art{position:absolute;left:111px;top:20px;width:570px;height:315px;
  background:linear-gradient(120deg,#c9d2e0 0%,#9aa8c0 55%,var(--slate) 100%)}
.hero-copy{position:absolute;left:682px;top:110px;width:292px;color:#fff}
.hero-copy h1{font-size:22px;font-weight:400;letter-spacing:.2px;white-space:nowrap}
.hero-copy p{font-size:12.5px;line-height:21px;text-align:justify;letter-spacing:.4px;margin-top:4px;text-transform:uppercase}
.hero-cta{display:flex;align-items:center;gap:8px;margin-top:18px;font-size:13.5px}
.btn{background:var(--red);color:#fff;padding:6px 12px;text-decoration:none}
.hero-cta .alt{color:var(--link-blue);text-decoration:none}
.dots{position:absolute;left:936px;top:305px;display:flex;gap:5px}
.dots span{width:8px;height:8px;border-radius:50%;background:#8f96a3}
.dots span:nth-child(2){background:#3b3f46}

.nav{top:100px;height:40px;display:flex;background:linear-gradient(#6f7072,#555659);border:1px solid #444;z-index:2}
.nav a{color:#fff;text-decoration:none;font-size:13.5px;line-height:38px;padding:0 27px}
.nav a.current{background:var(--red);padding:0 20px}

/* credential cards */
.cards{top:473px;display:flex;gap:28px}
.card{width:277px;height:123px;background:var(--red);color:#fff;padding:6px 12px}
.card h2{font-size:23px;font-weight:700;line-height:30px}
.card .sub{font-size:13px}
.card .body{display:flex;gap:14px;align-items:center;margin-top:14px}
.card .body svg{flex:0 0 40px}
.card .body p{font-size:12px;line-height:14.5px;text-align:justify;hyphens:manual}

/* community */
.community-head{top:636px;text-align:center}
.community-head h2{font-size:23px;font-weight:400;color:#555}
.community-head p{font-size:17.5px;color:var(--red);margin-top:4px}

.col-title{font-size:17.5px;color:var(--red);font-weight:400}
.blog{position:absolute;left:111px;top:712px;width:280px}
.blog ul{list-style:none;margin-top:24px}
.blog li{font-size:11px;color:#666;line-height:28.7px;white-space:nowrap}
.blog li::before{content:"» ";color:#333}

.social{position:absolute;left:415px;top:712px;width:278px}
.post{display:flex;gap:10px;margin-top:8px}
.social .post:first-of-type{margin-top:22px}
.thumb{width:64px;height:64px;flex:0 0 64px}
.post p{font-size:12px;line-height:16.4px;text-align:justify;color:#444;hyphens:manual}

.in-community{position:absolute;left:711px;top:703px;width:278px;height:275px;background:var(--grey-dark);padding:9px 27px}
.in-community h3{font-size:18px;font-weight:400;color:#fff}
.grid{display:grid;grid-template-columns:91px 91px;column-gap:36px;row-gap:6px;margin-top:14px}
.grid figure{margin:0}
.grid .ph{width:91px;height:81px}
.grid figcaption{font-size:12px;color:#fff;margin-top:1px}

/* footer */
.footer{position:absolute;left:0;top:1011px;width:1108px;height:159px;background:var(--grey-footer);color:#fff}
.agent{position:absolute;left:111px;top:15px}
.agent .ph{width:157px;height:96px}
.agent b{display:block;font-size:14px;font-weight:400;margin-top:4px}
.agent small{font-size:10px}
.f-col{position:absolute;top:11px}
.f-col h4{font-size:17.5px;font-weight:400}
.address{left:323px;font-size:12px;line-height:16.6px}
.address p{margin-top:14px}
.address p+p{margin-top:18px}
.housing{left:600px}
.follow{left:794px}
.socials{display:flex;gap:7px;margin-top:15px}
.socials span{width:27px;height:27px;border-radius:4px;display:block}
.follow h4.lang{margin-top:21px}
.flags{display:flex;gap:5px;margin-top:6px}
.flags span{width:18px;height:11px;display:block}
.bottom{position:absolute;left:0;top:1170px;width:1108px;height:30px;background:var(--grey-bar);color:#fff;font-size:11.5px;text-align:center;line-height:30px}
</style>
</head>
<body>

<header>
  <div class="wrap brand">
    <span class="brand-name">Brookvale Funding</span>
    <span class="brand-tag">A Harlow Capital Company</span>
  </div>
  <div class="wrap contact-top">
    <div>WORK WITH US: <span class="hl">123 - 456 - 7890</span></div>
    <div class="hl">EMAIL HERE</div>
  </div>
</header>

<section class="hero">
  <div class="hero-art" role="img" aria-label="Illustration of white jigsaw puzzle pieces with houses, cars and trees, one gold piece with a dollar sign"></div>
  <div class="hero-copy">
    <h1>EARNING YOUR BUSINESS</h1>
    <p>The Marisol Kettering team relies on strong systems to deliver an on-time, done-right and friendly experience.</p>
    <div class="hero-cta"><a class="btn" href="#">START HERE</a><span>(OR)</span><a class="alt" href="#">GET TO KNOW US</a></div>
  </div>
  <div class="dots"><span></span><span></span><span></span></div>
</section>

<nav class="wrap nav">
  <a class="current" href="#">HOME</a><a href="#">ABOUT</a><a href="#">BUILDER INFO</a><a href="#">MORTGAGE INFO</a><a href="#">APPROVAL</a><a href="#">BLOG</a><a href="#">CONTACT</a>
</nav>

<section class="wrap cards">
  <article class="card">
    <h2>OUR CREDENTIALS</h2>
    <div class="sub">A top - Producer, Top - Notch</div>
    <div class="body">
      <svg width="40" height="32" viewBox="0 0 40 32" fill="none" stroke="#fff" stroke-width="2"><rect x="10" y="2" width="26" height="18"/><rect x="6" y="6" width="26" height="18" fill="var(--red)"/><rect x="2" y="10" width="26" height="18" fill="#fff"/></svg>
      <p>Lorem ipsum dolor sit amet, con&shy;sectetur adipisicing elit, sed do eius&shy;mod tempor incididunt</p>
    </div>
  </article>
  <article class="card">
    <h2>AWARDS</h2>
    <div class="sub">A top - Producer, Top - Notch</div>
    <div class="body">
      <svg width="40" height="40" viewBox="0 0 40 40" fill="none" stroke="#fff" stroke-width="2"><path d="M12 4h16l-5 12h-6z" fill="#fff"/><circle cx="20" cy="27" r="9"/><path d="M20 23v8"/></svg>
      <p>Lorem ipsum dolor sit amet, con&shy;sectetur adipisicing elit, sed do eius&shy;mod tempor incididunt</p>
    </div>
  </article>
  <article class="card">
    <h2>RECOGNITION</h2>
    <div class="sub">A top - Producer, Top - Notch</div>
    <div class="body">
      <svg width="40" height="40" viewBox="0 0 40 40" fill="none" stroke="#fff" stroke-width="3"><circle cx="20" cy="20" r="7"/><path d="M20 4v8M20 28v8M4 20h8M28 20h8M9 9l5 5M26 26l5 5M31 9l-5 5M14 26l-5 5"/></svg>
      <p>Lorem ipsum dolor sit amet, con&shy;sectetur adipisicing elit, sed do eius&shy;mod tempor incididunt</p>
    </div>
  </article>
</section>

<section class="wrap community-head">
  <h2>Engaged in Our Community</h2>
  <p>Connect with Us</p>
</section>

<section class="blog">
  <h3 class="col-title">Blog</h3>
  <ul>
    <li>Lorem ipsum dolor sit amet, consectetur adipiscing</li>
    <li>Sed pulvinar leo non faucibus bibendum.</li>
    <li>Aenean in quam ac metus venenatis commodo.</li>
    <li>Cras vehicula odio et posuere scelerisque.</li>
    <li>Nulla eu mauris sed massa consequat tempor vel</li>
    <li>Nam lobortis orci ut tellus pharetra volutpat ut a</li>
    <li>In a erat non magna bibendum molestie nec sed</li>
    <li>In a erat non magna bibendum molestie nec sed</li>
  </ul>
</section>

<section class="social">
  <h3 class="col-title">Social</h3>
  <div class="post"><div class="thumb" role="img" aria-label="Photo of a young woman with dark hair" style="background:linear-gradient(135deg,#d9cfc8,#6b5348)"></div><p>Lorem ipsum dolor sit amet, con&shy;sectetur adipiscing elit.Sed pulvinar leo nonfaucibus bibendum.Aenean in quam acnenatis commod</p></div>
  <div class="post"><div class="thumb" role="img" aria-label="Photo of a blonde woman in a yellow top" style="background:linear-gradient(135deg,#f1ece4,#d9b25a)"></div><p>Lorem ipsum dolor sit amet, con&shy;sectetur adipiscing elit.Sed pulvinar leo nonfaucibus bibendum.Aenean in quam acnenatis commod</p></div>
  <div class="post"><div class="thumb" role="img" aria-label="Photo of a smiling woman" style="background:linear-gradient(135deg,#e6d6c8,#a77f63)"></div><p>Lorem ipsum dolor sit amet, con&shy;sectetur adipiscing elit.Sed pulvinar leo nonfaucibus bibendum.Aenean in quam acnenatis commod</p></div>
</section>

<aside class="in-community">
  <h3>In the Community</h3>
  <div class="grid">
    <figure><div class="ph" role="img" aria-label="Photo of a student holding green folders" style="background:linear-gradient(#f2f2f2,#7fb24a)"></div><figcaption>Lorem ipsum</figcaption></figure>
    <figure><div class="ph" role="img" aria-label="Photo of a child writing in a classroom" style="background:linear-gradient(135deg,#5f9a86,#b6a2a4)"></div><figcaption>Lorem ipsum</figcaption></figure>
    <figure><div class="ph" role="img" aria-label="Photo of a young store worker in a red cap" style="background:linear-gradient(#7f8aa0,#d9322c)"></div><figcaption>Lorem ipsum</figcaption></figure>
    <figure><div class="ph" role="img" aria-label="Photo of a mother and daughter smiling" style="background:linear-gradient(135deg,#c9c1b6,#e2c79d)"></div><figcaption>Lorem ipsum</figcaption></figure>
  </div>
</aside>

<footer class="footer">
  <div class="agent">
    <div class="ph" role="img" aria-label="Portrait photo of Marisol Kettering" style="background:linear-gradient(135deg,#6b4a36,#c89a7c)"></div>
    <b>Marisol Kettering</b>
    <small>Senior Loan Officer</small>
  </div>
  <div class="f-col address">
    <h4>Our Address</h4>
    <p>Corporate Office - 2240 Elmridge Parkway,<br>Suite 410 Dallas, Texas 75201</p>
    <p>Tel : 1-800-555-0142<br>Email : Contact Brookvale Funding</p>
  </div>
  <div class="f-col housing">
    <h4>Equal Housing</h4>
    <svg width="110" height="110" viewBox="0 0 110 110" style="margin-top:4px"><rect x="5" y="10" width="100" height="95" rx="4" fill="#6e6f71"/></svg>
  </div>
  <div class="f-col follow">
    <h4>Follow Us</h4>
    <div class="socials"><span style="background:#3b6fc4"></span><span style="background:#3fa7e0"></span><span style="background:#2a8fc7"></span></div>
    <h4 class="lang">Misc Language</h4>
    <div class="flags">
      <span style="background:linear-gradient(#000 33%,#d00 33% 66%,#fc0 66%)"></span>
      <span style="background:linear-gradient(90deg,#0a3ea5 33%,#fff 33% 66%,#e0232b 66%)"></span>
      <span style="background:#23407f"></span>
    </div>
  </div>
</footer>
<div class="bottom">©2013 Marisol Kettering | All Rights Reserved.</div>

</body>
</html>
```